KLORA product web page

We need a new web design for our KLORA product page. You can find more information about the project on the current web site - www.klora.example

What we need from a new design (uncoded):
- landing pages + template
- all information on one page
- the design should be focused on the product - light bulb + app
- web site should be with some dynamics like a background with parallax effect in the current version
- fonts should be chosen
- a number of illustrations should be designed

Here is schema for a new design: https://files.examplehost.net/d/draw-7QpX2mLk9RtYv4Hs/edit

Here is a document with all texts for a new design: https://files.examplehost.net/d/doc-3WnZ8bJf5KcUe1Ga/edit

Illustrations to use:
v1 - https://files.examplehost.net/f/fold-A1kT9pQw2ZxR
v2 - https://files.examplehost.net/f/fold-B7mH4sLv6YcN

Phonix OS screens: https://files.examplehost.net/f/fold-C3rJ8dKe1WuP

KLORA logo: https://files.examplehost.net/f/fold-D5nF2gTb9XoM
Updates

I forgot to add the definition text "KLORA - is.." to the document with texts. Sorry, my mistake.

Target Market(s)

25-45 year old adults who are interested in "smart" devices for their health.

Industry/Entity Type

Brintel

Colors

Designer to choose colors to be used in the design.

Requirements
Must have
• - landing pages + template
- fonts should be chosen

```html
<!DOCTYPE html>
<html lang="en">
<head>
<meta charset="utf-8">
<title>KLORA — Wireless Lightbulbs</title>
<link href="https://fonts.googleapis.com/css2?family=Open+Sans:wght@400;600;700&display=swap" rel="stylesheet">
<style>
:root{
  --accent:#4bb8cc;
  --ink:#222;
  --dark:#252525;
  --dark-band:#2c2c2c;
  --muted:#8a8a8a;
  --white:#fff;
  --field:#ececec;
}
*{margin:0;padding:0;box-sizing:border-box}
html,body{width:1200px;height:2808px;overflow:hidden}
body{position:relative;font-family:'Open Sans',Arial,sans-serif;color:var(--ink);background:var(--white)}
.abs{position:absolute}
section,header,footer{position:absolute;left:0;width:1200px}

/* header */
.site-header{top:0;height:84px;background:var(--dark)}
.brand-name{left:172px;top:27px;color:var(--white);font-weight:700;font-size:22px;letter-spacing:2px}
.nav a{position:absolute;top:28px;height:30px;line-height:30px;color:var(--white);font-size:13px;text-decoration:none}
.nav .cta{background:var(--accent);padding:0 11px}

/* hero */
.hero{top:84px;height:500px}
.hero-photo{position:absolute;inset:0;background:linear-gradient(100deg,#6b3f22 0%,#a86a3c 30%,#3d6a94 55%,#7a4a2a 75%,#b27a48 100%)}
.tag{left:172px;top:84px;background:var(--accent);color:var(--white);font-size:10px;font-weight:600;padding:0 8px;height:27px;line-height:27px;text-transform:uppercase}
.hero-title{left:172px;top:124px;height:56px;line-height:56px;padding:0 13px;background:#262626;color:var(--white);font-size:21px;font-weight:700;white-space:nowrap;text-transform:uppercase}
.hero-sub{left:172px;top:193px;height:37px;line-height:37px;padding:0 10px;background:#262626;color:var(--white);font-size:14px;font-weight:700;white-space:nowrap}
.slide-arrow{top:234px;width:34px;height:34px}

/* headings */
.sec-title{left:0;width:1200px;text-align:center;font-weight:700;text-transform:uppercase}
.sec-title::after{content:"";display:block;width:56px;height:2px;background:currentColor;margin:10px auto 0}
.copy{font-size:10px;line-height:15px}
.copy p{margin-bottom:12px}

.welcome{top:584px;height:217px}
.welcome h1{font-size:26px;top:36px}
.welcome h1::after{display:none}
.welcome h1 span{color:var(--accent)}
.welcome .copy{left:219px;top:99px;width:775px;text-align:center;color:var(--muted)}

.features-dark{top:801px;height:453px;background:var(--dark-band);color:var(--white)}
.features-dark h2{font-size:21px}
.photo{position:absolute}
.features-light{top:1254px;height:502px}
.features-light h2{font-size:21px}

.specs{top:1756px;height:331px;background:var(--accent);color:var(--white)}
.specs h2{font-size:21px;top:39px}

.signup{top:2087px;height:268px}
.signup h2{left:513px;top:64px;font-size:20px;font-weight:700;text-transform:uppercase}
.signup h2::after{content:"";display:block;width:48px;height:2px;background:var(--ink);margin-top:10px}
.email-field{left:511px;top:158px;width:294px;height:43px;background:var(--field);font-size:13px;color:#555;line-height:43px;padding-left:16px}
.email-btn{left:805px;top:158px;width:54px;height:43px;background:var(--accent);display:flex;align-items:center;justify-content:center}

.site-footer{top:2355px;height:453px;background:var(--dark);color:#9a9a9a}
.footer h3{font-size:12px;font-weight:700;color:var(--white);text-transform:uppercase}
.field{border:1px solid #555;color:#777;font-size:9px;padding:8px 10px;text-transform:uppercase}
.social{display:flex;gap:11px}
.social i{display:block;width:11px;height:11px;border-radius:50%;background:#3d3d3d}
.contact-line{display:flex;align-items:center;gap:8px;font-size:11px}
</style>
</head>
<body>

<header class="site-header">
  <div class="brand-name abs">KLORA</div>
  <nav class="nav">
    <a class="cta" style="left:693px">Pre Order</a>
    <a style="left:807px">Blog</a>
    <a style="left:874px">Contacts</a>
    <a style="left:966px">RU</a>
  </nav>
</header>

<section class="hero">
  <div class="hero-photo" role="img" aria-label="Photo of a white ribbed KLORA smart lightbulb on a wooden table"></div>
  <div class="tag abs">Wireless lightbulbs</div>
  <div class="hero-title abs">Praesent posuere eros in</div>
  <div class="hero-sub abs">quam dictum,quis dignissim odio</div>
  <svg class="slide-arrow abs" style="left:4px" viewBox="0 0 34 34"><circle cx="17" cy="17" r="17" fill="#4bb8cc"/><path d="M19 11l-6 6 6 6" stroke="#fff" stroke-width="2.5" fill="none"/></svg>
  <svg class="slide-arrow abs" style="left:1157px" viewBox="0 0 34 34"><circle cx="17" cy="17" r="17" fill="#4bb8cc"/><path d="M15 11l6 6-6 6" stroke="#fff" stroke-width="2.5" fill="none"/></svg>
</section>

<section class="welcome">
  <h1 class="sec-title abs">Welcome to <span>KLORA</span></h1>
  <p class="copy abs">Lorem ipsum sit amet in quam dictum, quis dignissim odio suscipit. Integer luctus mi sit amet orci porttitor, at malesuada mauris sodales. Mauris vitae ipsum sed risus. Praesent posuere eros in quam dictum, quis dignissim odio suscipit. Integer luctus mi sit amet orci porttitor, at malesuada mauris sodales. Mauris vitae ipsum sed risus. Praesent posuere eros in quam dictum, quis dignissim odio suscipit. Integer luctus mi sit amet orci porttitor, at malesuada mauris sodales. Mauris vitae ipsum sed risus.</p>
</section>

<section class="features-dark">
  <h2 class="sec-title abs" style="top:52px">KLORA App</h2>
  <div class="photo" style="left:200px;top:112px;width:217px;height:132px;background:linear-gradient(90deg,#e8eef2,#9bb3c4 50%,#d8c7a6)" role="img" aria-label="Smartphone running the KLORA app next to a lit bulb"></div>
  <p class="copy abs" style="left:473px;top:107px;width:540px">KLORA Application allows you to control each lightbulb at home. Manage your lighting by creating functional groups and adding/excluding lightbulbs. Correctly matched lighting will help you work more productively and relax to the outmost. Create light scenes and adapt them to your needs. KLORA App memorizes your favorite moods, so that you can use your settings anytime. Play with million colors and adjust the brightness of your home lighting. KLORA works on Phonix OS 6+ and Droidline 4+.</p>

  <h2 class="sec-title abs" style="top:272px;left:-200px">KLORA and Color</h2>
  <div class="photo" style="left:794px;top:274px;width:217px;height:132px;background:linear-gradient(90deg,#1a2a3a,#c24a3a 35%,#2e9a4e 60%,#3a6ec0 85%,#1a2230)" role="img" aria-label="Three bulbs glowing in different colors"></div>
  <p class="copy abs" style="left:198px;top:349px;width:542px">Experiment with millions of colors! Pick any color from the screen of your mobile device and enjoy the ambience. LED lightbulb KLORA can transform conventional lighting into the night lights of Seattle or bring in the rich summer hues of Provence. Enliven your fantasies or raise your best memories in one click. Change the atmosphere around you by changing colors. You will literally see the world in a new light.</p>
</section>

<section class="features-light">
  <h2 class="sec-title abs" style="top:50px">KLORA and Health</h2>
  <div class="photo" style="left:200px;top:90px;width:216px;height:131px;background:radial-gradient(circle at 65% 50%,#fff4dc,#c8955a 30%,#2a1e14 70%)" role="img" aria-label="Bulb glowing warm white in a dark room"></div>
  <div class="copy abs" style="left:489px;top:122px;width:540px;color:#444">
    <p>Choose a scene for setting the alarm and improve your sleep naturally. KLORA lighting system creates the necessary conditions for normalizing your circadian rhythms. Set your smart lightbulbs to turn on: now you can wake up "on the sunny side" despite gloomy weather. KLORA lighting system will reduce your stress level.</p>
    <p>10 preset moods provide positive impact on your health. Designed to be what your mind and body need. We developed predefined modes in accordance with physiological and psychological aspects of human activities.</p>
  </div>

  <h2 class="sec-title abs" style="top:272px">Lighting Design</h2>
  <div class="copy abs" style="left:206px;top:333px;width:543px;color:#444">
    <p>Wireless lightbulbs with LinkWave and MeshBee help you implement the concept of the smart home. KLORA makes it affordable. Real lighting design at your place, couldn't have been simpler.</p>
    <p>Create optimal lighting for each functional area - set the perfect light for your kitchen, living room and nursery. Name individual lightbulbs or groups of them, set your color mood, pick a palette for each room. Stay informed of every smart lightbulb's condition, save your settings and load them anytime.</p>
    <p>With KLORA lightbulbs your home lighting fits your lifestyle perfectly!</p>
  </div>
  <div class="photo" style="left:809px;top:324px;width:215px;height:133px;background:linear-gradient(120deg,#2c4a8a,#5a86c8 50%,#1e2e58)" role="img" aria-label="Two hanging bulbs glowing against a blue wall"></div>
</section>

<section class="specs">
  <h2 class="sec-title abs">KLORA Technical Specifications</h2>
  <div class="photo" style="left:195px;top:99px;width:200px;height:193px;background:linear-gradient(160deg,#5a3a28,#c9a27a 45%,#e8eef3 70%,#9a7a5a)" role="img" aria-label="Hand holding a phone with the app beside a lit bulb"></div>
  <div class="copy abs" style="left:429px;top:97px;width:620px">
    <p>KLORA lightbulb is a 85W incandescent equivalent that transforms your visual environment.</p>
    <p>E27 socket: no need to change anything. Easy way to home automation at hand. And yet, you can still use those switches.</p>
    <p>12.5W (110 - 230V,50Hz), 1000lm+: energy efficient LED lightbulb KLORA shines brighter than others and saves energy.</p>
    <p>2700-5500K: You are not limited in your choice of color temperature. Turn on warm or cold light depending on your activities.</p>
    <p>Compatibility:<br>Phonix 4S/5/5C/5S<br>Tablo 3/4/Air/mini/mini Air<br>Tunepod 5th generation or newer<br>All Droidline devices with LinkWave 2.1 or 4</p>
  </div>
</section>

<section class="signup">
  <div class="photo" style="left:346px;top:38px;width:88px;height:193px;border-radius:44px 44px 20px 20px;background:linear-gradient(90deg,#8a5a3a,#e0b894 50%,#8a5a3a)" role="img" aria-label="Product shot of a KLORA bulb with copper-toned shell"></div>
  <h2 class="abs">Get your KLORA</h2>
  <p class="abs" style="left:511px;top:131px;font-size:11px">Enter your e-mail and we will notify you when it's available</p>
  <div class="email-field abs">Email Adress</div>
  <div class="email-btn abs"><svg width="22" height="16" viewBox="0 0 22 16"><rect x="1" y="1" width="20" height="14" fill="none" stroke="#fff" stroke-width="2"/><path d="M1 1l10 8 10-8" fill="none" stroke="#fff" stroke-width="2"/></svg></div>
</section>

<footer class="site-footer footer">
  <svg class="abs" style="left:173px;top:37px" width="18" height="18" viewBox="0 0 18 18"><circle cx="9" cy="9" r="9" fill="#fff"/></svg>
  <p class="abs" style="left:219px;top:34px;width:520px;font-size:12px;line-height:21px">RT @marlowe: Trade growth ideas with other founders. Look for ways to cross promote. Small startups today may be big friends later. (9/10) <span style="color:#555">2 days ago</span></p>
  <div class="social abs" style="left:852px;top:39px"><i></i><i></i><i></i><i></i><i></i><i></i><i></i></div>
  <div class="abs" style="left:176px;top:88px;width:908px;height:1px;background:#383838"></div>

  <h3 class="abs" style="left:206px;top:143px">Contact info</h3>
  <p class="abs" style="left:206px;top:176px;width:300px;font-size:11px;line-height:18px">Ut volutpat consectetur aliquam. Curabitur auctor in nis ulum ornare. Sed consequat, augue condimentum fermentum gravida, metus elit vehicula dui.</p>
  <div class="contact-line abs" style="left:206px;top:246px"><svg width="8" height="12" viewBox="0 0 8 12"><rect x="0.75" y="0.75" width="6.5" height="10.5" rx="1" fill="none" stroke="#bbb" stroke-width="1.5"/><rect x="3" y="8.6" width="2" height="1.2" fill="#bbb"/></svg><span>+1 555 0148 2290</span></div>
  <div class="contact-line abs" style="left:206px;top:265px"><svg width="10" height="8" viewBox="0 0 10 8"><rect x="0.5" y="0.5" width="9" height="7" fill="none" stroke="#bbb"/><path d="M0.5 0.5l4.5 4 4.5-4" fill="none" stroke="#bbb"/></svg><span>hello@klora.example</span></div>

  <h3 class="abs" style="left:618px;top:143px">Send us a message</h3>
  <div class="field abs" style="left:618px;top:181px;width:106px;height:29px">Your name</div>
  <div class="field abs" style="left:726px;top:181px;width:178px;height:29px">Email address</div>
  <div class="field abs" style="left:618px;top:226px;width:378px;height:96px">Your name</div>
  <div class="abs" style="left:618px;top:346px;width:181px;height:30px;background:var(--accent);color:#fff;font-size:11px;font-weight:700;line-height:30px;padding-left:18px;text-transform:uppercase">Submit your message &nbsp;›</div>
  <p class="abs" style="left:614px;top:400px;font-size:10px;color:#555">Make sure you put a valid email</p>

  <p class="abs" style="left:176px;top:423px;font-size:10px;color:#555">© 2014. All rights reserved</p>
  <p class="abs" style="left:1045px;top:423px;font-size:10px;color:var(--accent);text-decoration:underline">Back to top</p>
</footer>

</body>
</html>
```